Simple and Clean business card design

We would like the design to be simple clean and to incorporate our colors.

We are open to your design and talent, we have the dots in our logo as we think of it as data points and we connect data points for people.

We are open to see the great creative and clean design you bring to the table

Contact Information for Business Card

please include: name, position, email, phone and website

Font styles to use
Sans Serif

Requirements
Must have
• my colors incorporated, simplicity
Nice to have
• lots of white space, simplicity
Should not have
• complexicity/ complex art

```html
<!DOCTYPE html>
<html lang="en">
<head>
<meta charset="utf-8">
<title>Nectra Business Card</title>
<link rel="stylesheet" href="https://fonts.googleapis.com/css2?family=Open+Sans:wght@400;600&family=Saira:wght@600;700&display=swap">
<style>
  :root {
    --ink: #000000;
    --paper: #fdfdfd;
    --card-white: #ffffff;
    --brand-blue: #4285f4;
    --text-dark: #222222;
    --edge: #555555;
  }
  html, body {
    margin: 0;
    padding: 0;
    width: 1200px;
    height: 1200px;
    overflow: hidden;
    background: var(--paper);
  }
  .sheet {
    position: relative;
    width: 1200px;
    height: 1200px;
  }
  .card {
    position: absolute;
    left: 216px;
    width: 775px;
    height: 430px;
    box-sizing: border-box;
    overflow: hidden;
  }
  .card-front {
    top: 147px;
    background: var(--ink);
    display: flex;
    align-items: center;
    justify-content: center;
  }
  .card-back {
    top: 630px;
    background: var(--card-white);
    border: 1px solid var(--edge);
  }
  .wordmark {
    display: inline-flex;
    align-items: flex-end;
    font-family: "Open Sans", sans-serif;
    font-weight: 600;
    line-height: 1;
    letter-spacing: -1px;
    white-space: nowrap;
  }
  .wordmark-dot {
    border-radius: 50%;
    flex: none;
  }
  .card-front .wordmark {
    gap: 10px;
    font-size: 104px;
    color: var(--card-white);
    margin-top: 10px;
  }
  .card-front .wordmark-dot {
    width: 22px;
    height: 22px;
    background: var(--card-white);
    margin-bottom: 16px;
  }
  .card-back .wordmark {
    position: absolute;
    left: 50px;
    top: 178px;
    gap: 8px;
    font-size: 82px;
    color: var(--ink);
  }
  .card-back .wordmark-dot {
    width: 18px;
    height: 18px;
    background: var(--brand-blue);
    margin-bottom: 13px;
  }
  .contact-name {
    position: absolute;
    left: 387px;
    top: 112px;
    margin: 0;
    font-family: "Saira", sans-serif;
    font-weight: 700;
    font-size: 40px;
    line-height: 1;
    letter-spacing: 1px;
    color: var(--brand-blue);
  }
  .contact-role {
    position: absolute;
    left: 389px;
    top: 160px;
    margin: 0;
    font-family: "Saira", sans-serif;
    font-weight: 600;
    font-size: 20px;
    line-height: 1;
    letter-spacing: 2px;
    color: var(--ink);
  }
  .contact-rule {
    position: absolute;
    left: 390px;
    top: 192px;
    width: 349px;
    height: 2px;
    background: var(--brand-blue);
    border: 0;
    margin: 0;
  }
  .contact-list {
    position: absolute;
    left: 386px;
    top: 209px;
    margin: 0;
    padding: 0;
    list-style: none;
  }
  .contact-item {
    display: flex;
    align-items: center;
    height: 33px;
    font-family: "Open Sans", sans-serif;
    font-size: 20px;
    color: var(--text-dark);
  }
  .contact-icon {
    width: 26px;
    height: 26px;
    margin-right: 14px;
    flex: none;
  }
  .accent-band {
    position: absolute;
    left: 0;
    bottom: 0;
    width: 100%;
    height: 22px;
    display: flex;
  }
  .accent-band-dark { flex: 1; background: var(--ink); }
  .accent-band-blue { flex: 1; background: var(--brand-blue); }
</style>
</head>
<body>
<main class="sheet">
  <section class="card card-front" aria-label="Card front">
    <div class="wordmark">Nectra<span class="wordmark-dot"></span></div>
  </section>

  <section class="card card-back" aria-label="Card back">
    <div class="wordmark">Nectra<span class="wordmark-dot"></span></div>

    <h1 class="contact-name">DANIEL MOORE</h1>
    <p class="contact-role">CEO/FOUNDER</p>
    <hr class="contact-rule">

    <ul class="contact-list">
      <li class="contact-item">
        <svg class="contact-icon" viewBox="0 0 24 24" aria-hidden="true">
          <path d="M6.6 10.8c1.4 2.8 3.8 5.1 6.6 6.6l2.2-2.2c.3-.3.7-.4 1-.2 1.1.4 2.3.6 3.6.6.6 0 1 .4 1 1V20c0 .6-.4 1-1 1C10.6 21 3 13.4 3 4c0-.6.4-1 1-1h3.5c.6 0 1 .4 1 1 0 1.3.2 2.5.6 3.6.1.3 0 .7-.2 1z" fill="var(--brand-blue)"/>
        </svg>
        <span>780-555-0192</span>
      </li>
      <li class="contact-item">
        <svg class="contact-icon" viewBox="0 0 26 26" aria-hidden="true" fill="none" stroke="var(--brand-blue)" stroke-width="1.3">
          <circle cx="13" cy="13" r="11.5"/>
          <ellipse cx="13" cy="13" rx="5" ry="11.5"/>
          <line x1="13" y1="1.5" x2="13" y2="24.5"/>
          <line x1="1.5" y1="13" x2="24.5" y2="13"/>
          <path d="M3.5 7 H22.5 M3.5 19 H22.5"/>
        </svg>
        <span>www.nectra.one</span>
      </li>
      <li class="contact-item">
        <svg class="contact-icon" viewBox="0 0 26 26" aria-hidden="true">
          <rect x="2" y="6" width="22" height="15" fill="var(--brand-blue)"/>
          <path d="M2.5 6.5 L13 14.5 L23.5 6.5 M2.5 20.5 L10 13 M23.5 20.5 L16 13" fill="none" stroke="var(--card-white)" stroke-width="1.2"/>
        </svg>
        <span>daniel.moore@nectra.one</span>
      </li>
    </ul>

    <div class="accent-band">
      <span class="accent-band-dark"></span>
      <span class="accent-band-blue"></span>
    </div>
  </section>
</main>
</body>
</html>
```